Landing page design for my current website

I need a landing page designed for my Wordpress website. My website is Velmorquay.com, and I need a page that will serve as a landing page for online ads I run. Please follow the color scheme of the current website

This web page will be targeted towards real estate owners who are looking for a property manager. Above the fold needs to have a CTA form headlined with "As a Rental Property Owner, I Want More Protection, Less Stress, and Drama-Free Living"

A few highlights that can be listed beyond the CTA and fold

- Comprehensive Property Management
Full-service management covering tenant placement, leasing, maintenance, and inspections.

Maximized Rental Income
Proven strategies to optimize rental rates and minimize vacancies, ensuring higher ROI.

Stress-Free Management
We handle all tenant interactions, maintenance requests, and property issues, so you don't have to.

Experienced Team
Over a decade of experience in managing single-family homes, small multifamily units, and apartment complexes.

Advanced Technology
Utilize cutting-edge property management software for efficient communication, rent collection, and maintenance tracking.

Tenant Screening and Placement
Thorough background checks and tenant screening processes to ensure reliable and responsible tenants.

Regular Property Inspections
Routine inspections to maintain property condition and address issues before they become costly problems.

Legal Compliance
Expertise in local and federal rental laws to keep your properties compliant and avoid legal hassles.

Transparent Reporting
Detailed monthly reports and financial statements to keep you informed about your property's performance.

Personalized Service
Tailored management plans to meet the unique needs of your properties and investment goals.
Effective Tenant Conflict Resolution
Skilled in handling challenging tenant situations, ensuring conflicts are resolved quickly and professionally to maintain a peaceful living environment and protect your investment.

```html
<!DOCTYPE html>
<html lang="en">
<head>
<meta charset="utf-8">
<title>Velmorquay Realty – Property Management</title>
<link href="https://fonts.googleapis.com/css2?family=Poppins:wght@400;500;600;700;800&display=swap" rel="stylesheet">
<style>
:root{
  --brand:#134478;
  --brand-bright:#1a5496;
  --ink:#111111;
  --dark:#333333;
  --text:#2b2b2b;
  --field:#f3f3f3;
  --panel:#f6f7f9;
  --white:#ffffff;
  --rule:#e6e6e6;
}
*{margin:0;padding:0;box-sizing:border-box}
html,body{width:734px;height:1200px;overflow:hidden}
body{position:relative;font-family:'Poppins',sans-serif;color:var(--text);background:var(--white)}

/* header */
.site-header{position:absolute;left:0;top:0;width:734px;height:41px;background:var(--white)}
.brand{position:absolute;left:68px;top:8px;display:flex;align-items:center;gap:6px}
.brand-dot{width:26px;height:26px;border-radius:50%;border:2px solid var(--brand)}
.brand-name{font-weight:600;font-size:12px;letter-spacing:.5px;color:var(--brand)}
.header-phone{position:absolute;left:417px;top:16px;display:flex;align-items:center;gap:6px;font-size:8.5px;color:var(--ink)}
.header-cta{position:absolute;left:516px;top:0;width:113px;height:41px;background:var(--brand);color:var(--white);font-weight:700;font-size:7.8px;display:flex;align-items:center;justify-content:center}
.menu-icon{position:absolute;left:649px;top:16px;width:14px}
.menu-icon span{display:block;height:2px;background:var(--ink);margin-bottom:3.5px}

/* hero */
.hero{position:absolute;left:0;top:41px;width:734px;height:390px;overflow:hidden}
.hero-photo{position:absolute;inset:0;background:linear-gradient(180deg,#0d3d97 0%,#2a63b6 28%,#8e99a6 52%,#6d6a62 75%,#3f4a34 100%)}
.hero-shade{position:absolute;inset:0;background:linear-gradient(90deg,rgba(0,0,0,.18),rgba(0,0,0,0) 70%)}
.hero-welcome{position:absolute;left:69px;top:142px;font-weight:700;font-size:15px;color:var(--white)}
.hero-title{position:absolute;left:69px;top:170px;font-weight:800;font-size:32px;letter-spacing:-.3px;color:var(--white);white-space:nowrap}
.hero-sub{position:absolute;left:69px;top:216px;font-size:16.5px;color:var(--white)}
.hero-btn{position:absolute;left:68px;top:255px;width:106px;height:36px;background:var(--white);color:var(--ink);font-weight:700;font-size:8px;display:flex;align-items:center;justify-content:center}

.lead-form{position:absolute;left:450px;top:32px;width:268px;height:338px;background:var(--panel)}
.lead-form h2{position:absolute;left:15px;top:17px;width:245px;font-weight:600;font-size:13.6px;line-height:20.5px;color:var(--ink)}
.lead-form h2 em{font-style:normal;color:var(--brand-bright)}
.field{position:absolute;height:30px;background:var(--field);box-shadow:0 1px 2px rgba(0,0,0,.08);font-size:8.5px;color:#555;padding-left:17px;display:flex;align-items:center}
.field svg{position:absolute;right:10px;top:12px}
.policy{position:absolute;left:24px;top:252px;font-size:8.6px;color:#555}
.policy u{color:var(--brand-bright)}
.submit{position:absolute;left:16px;top:285px;width:237px;height:30px;background:var(--brand);color:var(--white);font-weight:600;font-size:8.3px;display:flex;align-items:center;justify-content:center}

/* features */
.features-title{position:absolute;left:0;top:480px;width:734px;text-align:center;font-weight:700;font-size:27px;color:var(--ink);letter-spacing:-.2px}
.features-title span{color:var(--brand)}
.features-rule{position:absolute;left:299px;top:521px;width:121px;height:2px;background:var(--rule)}
.diagram{position:absolute;left:0;top:0;width:734px;height:1200px}
.feature{position:absolute;font-size:8px;line-height:12.6px;color:var(--text)}
.feature h3{font-weight:500;font-size:9px;color:var(--ink);line-height:12.6px;margin-bottom:3.5px}
.feature.right{text-align:right}
.feature.center{text-align:center}

/* footer */
.site-footer{position:absolute;left:0;top:1027px;width:734px;height:173px;background:var(--brand);color:var(--white)}
.footer-brand{position:absolute;left:67px;top:53px;display:flex;align-items:center;gap:7px}
.footer-brand .brand-dot{border-color:var(--white);width:30px;height:30px}
.footer-brand .brand-name{color:var(--white);font-size:15px}
.socials{position:absolute;left:561px;top:46px;display:flex;gap:5.5px}
.socials span{width:20px;height:20px;border-radius:50%;background:var(--white)}
.contact{position:absolute;display:flex;gap:10px;font-size:9px;line-height:16px}
.footer-rule{position:absolute;left:68px;top:149px;width:597px;height:1px;background:rgba(255,255,255,.85)}
.copyright{position:absolute;left:68px;top:157px;font-size:7px}
.legal-links{position:absolute;right:69px;top:156px;font-size:7px;display:flex;gap:5px;align-items:center}
.legal-links i{width:1.5px;height:9px;background:var(--white)}
</style>
</head>
<body>

<header class="site-header">
  <div class="brand"><span class="brand-dot"></span><span class="brand-name">VELMORQUAY REALTY</span></div>
  <div class="header-phone">
    <svg width="13" height="13" viewBox="0 0 24 24"><path fill="#134478" d="M6.6 10.8a15.1 15.1 0 0 0 6.6 6.6l2.2-2.2c.3-.3.7-.4 1-.2 1.1.4 2.3.6 3.6.6.6 0 1 .4 1 1V20c0 .6-.4 1-1 1A17 17 0 0 1 3 4c0-.6.4-1 1-1h3.5c.6 0 1 .4 1 1 0 1.3.2 2.5.6 3.6.1.3 0 .7-.2 1z"/></svg>
    555.014.2290
  </div>
  <div class="header-cta">GET A FREE ESTIMATE</div>
  <div class="menu-icon"><span></span><span></span><span></span></div>
</header>

<section class="hero">
  <div class="hero-photo" role="img" aria-label="Photo of a two-storey suburban house with grey siding, white trim and a stone porch under a deep blue sky"></div>
  <div class="hero-shade"></div>
  <p class="hero-welcome">Welcome To</p>
  <h1 class="hero-title">VELMORQUAY REALTY</h1>
  <p class="hero-sub">Excellence In Tenant Experience</p>
  <div class="hero-btn">GET STARTED</div>

  <form class="lead-form">
    <h2>As a <em>Rental Property Owner</em>, I Want More Protection, Less Stress, and Drama-Free Living</h2>
    <div class="field" style="left:15px;top:86px;width:239px">Full Name</div>
    <div class="field" style="left:15px;top:122px;width:239px">Email Address</div>
    <div class="field" style="left:16px;top:159px;width:112px">Phone Number</div>
    <div class="field" style="left:140px;top:159px;width:112px">Zip Code</div>
    <div class="field" style="left:15px;top:200px;width:239px">Interest
      <svg width="9" height="6" viewBox="0 0 9 6"><path d="M1 1l3.5 3.5L8 1" stroke="#111" stroke-width="1.3" fill="none"/></svg>
    </div>
    <p class="policy">Form submission agrees to <u>privacy policy</u></p>
    <div class="submit">SUBMIT NOW</div>
  </form>
</section>

<h2 class="features-title">OUR <span>FEATURES</span></h2>
<div class="features-rule"></div>

<svg class="diagram" viewBox="0 0 734 1200">
  <ellipse cx="365" cy="722" rx="136" ry="142" fill="none" stroke="#333" stroke-width="2.2"/>
  <circle cx="368" cy="718" r="92" fill="#f4f6f9"/>
  <text x="368" y="722" text-anchor="middle" font-family="Poppins, sans-serif" font-weight="700" font-size="15" fill="#134478">VELMORQUAY</text>
  <g>
    <circle cx="291.5" cy="588" r="23.5" fill="#134478"/>
    <circle cx="238.5" cy="644" r="23.5" fill="#333"/>
    <circle cx="230.5" cy="726" r="23.5" fill="#134478"/>
    <circle cx="249" cy="797.5" r="23.5" fill="#333"/>
    <circle cx="295.7" cy="843.6" r="23.5" fill="#134478"/>
    <circle cx="364" cy="863.5" r="23.5" fill="#333"/>
    <circle cx="447" cy="844.6" r="23.5" fill="#134478"/>
    <circle cx="492" cy="795" r="23.5" fill="#333"/>
    <circle cx="500" cy="729" r="23.5" fill="#134478"/>
    <circle cx="495.5" cy="657" r="23.5" fill="#333"/>
    <circle cx="455" cy="593.5" r="23.5" fill="#134478"/>
  </g>
</svg>

<div class="feature right" style="right:474px;top:550px;width:210px">
  <h3>Personalized Service</h3>
  <p style="margin-right:4px">Tailored management plans to meet the unique needs of your properties and investment goals.</p>
</div>
<div class="feature right" style="right:528px;top:619px;width:180px">
  <h3>Comprehensive Property Management</h3>
  <p style="margin-right:4px">Full-service management covering tenant placement, leasing, maintenance, and inspections.</p>
</div>
<div class="feature right" style="right:537px;top:708px;width:200px">
  <h3>Maximized Rental Income</h3>
  <p style="margin-top:3px">Proven strategies to optimize rental rates and minimize vacancies, ensuring higher ROI.</p>
</div>
<div class="feature right" style="right:521px;top:787px;width:190px">
  <h3>Stress-Free Management</h3>
  <p>We handle all tenant interactions, maintenance requests, and property issues, so you don't have to.</p>
</div>
<div class="feature right" style="right:463px;top:867px;width:180px">
  <h3>Experienced Team</h3>
  <p>Over a decade of experience in managing single-family homes, small multifamily units, and apartment complexes.</p>
</div>
<div class="feature center" style="left:288px;top:903px;width:150px">
  <h3>Advanced Technology</h3>
  <p>Utilize cutting-edge property management software for efficient communication, rent collection, and maintenance tracking.</p>
</div>
<div class="feature" style="left:468px;top:869px;width:180px">
  <h3>Tenant Screening and Placement</h3>
  <p>Thorough background checks and tenant screening processes to ensure reliable and responsible tenants.</p>
</div>
<div class="feature" style="left:528px;top:787px;width:185px">
  <h3>Regular Property Inspections</h3>
  <p>We handle all tenant interactions, maintenance requests, and property issues, so you don't have to.</p>
</div>
<div class="feature" style="left:534px;top:719px;width:196px">
  <h3>Legal Compliance</h3>
  <p style="margin-left:3px">Proven strategies to optimize rental rates and minimize vacancies, ensuring higher ROI.</p>
</div>
<div class="feature" style="left:531px;top:636px;width:195px">
  <h3 style="margin-bottom:6px">Transparent Reporting</h3>
  <p style="margin-left:2px">Detailed monthly reports and financial statements to keep you informed about your property's performance.</p>
</div>
<div class="feature" style="left:507px;top:557px;width:205px">
  <h3>Effective Tenant Conflict Resolution</h3>
  <p style="margin-left:2px">Skilled in handling challenging tenant situations, ensuring conflicts are resolved quickly and professionally to maintain a peaceful living environment and protect your investment.</p>
</div>

<footer class="site-footer">
  <div class="footer-brand"><span class="brand-dot"></span><span class="brand-name">VELMORQUAY REALTY</span></div>
  <div class="socials"><span></span><span></span><span></span><span></span></div>

  <div class="contact" style="left:68px;top:101px">
    <svg width="16" height="16" viewBox="0 0 24 24"><circle cx="12" cy="12" r="12" fill="#fff"/><path fill="#134478" d="M12 5a5 5 0 0 0-5 5c0 3.8 5 9 5 9s5-5.2 5-9a5 5 0 0 0-5-5zm0 7a2 2 0 1 1 0-4 2 2 0 0 1 0 4z"/></svg>
    <span>18 Harlow Lane,<br>Fenwick PA, 17920</span>
  </div>
  <div class="contact" style="left:236px;top:106px">
    <svg width="18" height="18" viewBox="0 0 24 24"><circle cx="12" cy="12" r="12" fill="#fff"/><path fill="#134478" d="M8.6 11.2a9 9 0 0 0 4.2 4.2l1.4-1.4c.2-.2.5-.3.7-.1.7.2 1.5.4 2.3.4.4 0 .6.3.6.6v2.2c0 .4-.3.6-.6.6A10.8 10.8 0 0 1 6.5 6.9c0-.4.3-.6.6-.6h2.2c.4 0 .6.3.6.6 0 .8.1 1.6.4 2.3.1.3 0 .5-.1.7z"/></svg>
    <span style="margin-left:1px">555.014.2290</span>
  </div>
  <div class="contact" style="left:367px;top:107px">
    <svg width="18" height="18" viewBox="0 0 24 24"><circle cx="12" cy="12" r="12" fill="#fff"/><rect x="6" y="8" width="12" height="8.5" rx="1" fill="#134478"/><path d="M6.5 8.7l5.5 4.3 5.5-4.3" stroke="#fff" stroke-width="1" fill="none"/></svg>
    <span style="margin-left:2px">Hello@velmorquay.com</span>
  </div>

  <div class="footer-rule"></div>
  <p class="copyright">Copyright © 2024 velmorquay realty.All rights reserved.</p>
  <div class="legal-links"><span>Privacy Policy</span><i></i><span>Terms &amp; Conditions</span></div>
</footer>

</body>
</html>
```